Velvet Circle club

We are looking to redesign the user interface of our mobile app “Velvet Circle”, which is the official rewards program for our luxury casino brand, Kestrane Harbour.
Our goal is to give the app a more elegant, premium, and user-friendly design that reflects the exclusivity of our brand and the luxury experience we offer our VIP clientele.
What We Need:
A complete UI design for the app’s main screens, including:
Splash Screen
01 Login / Signup Screen
02 Home Dashboard
Buttons -
Home / my card / my wallet / my booking / my host
My wallet / my offer / lucky game / my taxi / entertainment / online
03 Profile screen
04 My wallet
05 My offer
06Packages
07 My booking
08 My host
09 My card
we attached our privies app all the screen for you reference
Inspiration:
Think of luxury brands like Dunmore-Vale, Corvix Onyx, or high-end lifestyle apps. Clean interfaces, classy animations, and a sense of exclusivity are key.
We’re excited to see fresh, innovative takes that elevate the app to a truly world-class luxury experience for our users.
Thank you!
Casino

```html
<!DOCTYPE html>
<html lang="en">
<head>
<meta charset="utf-8">
<title>Velvet Circle – App Screens</title>
<link rel="stylesheet" href="https://fonts.googleapis.com/css2?family=Lexend:wght@400;600&family=Nunito+Sans:wght@400;600;700&display=swap">
<style>
:root{
  --canvas:#efefeb;
  --screen:#f7f6f3;
  --white:#ffffff;
  --header:#c9bec0;
  --ink:#1f1d1d;
  --muted:#8a8585;
  --line:#dedad6;
  --olive:#8b7b61;
  --gold:#a8905e;
  --brand:#c9452f;
  --tile:#f1efec;
  --disabled:#a7a5a3;
}
*{box-sizing:border-box;margin:0;padding:0}
html,body{width:1200px;height:968px;overflow:hidden}
body{background:var(--canvas);font-family:"Nunito Sans",sans-serif;color:var(--ink);position:relative}
.title{position:absolute;font-family:"Lexend",sans-serif;font-size:19px;line-height:23px;text-align:center;width:220px;color:#151515;letter-spacing:.2px}
.phone{position:absolute;width:161px;background:var(--screen);border-radius:14px;overflow:hidden;box-shadow:0 3px 8px rgba(0,0,0,.07)}
.phone.soft{background:linear-gradient(#fbfbfa,#eeedea)}
.sb{display:flex;justify-content:space-between;align-items:center;padding:6px 11px 0;font-size:5.5px;font-weight:700;height:14px}
.sb svg{height:5px;width:20px}
.brand{text-align:center;font-family:"Lexend",sans-serif;font-weight:600;color:var(--brand);line-height:1}
.brand .dot{width:11px;height:11px;border-radius:50%;background:var(--brand);margin:0 auto 4px}
.brand .name{font-size:13px}
.brand .club{font-size:6px;margin-top:2px;letter-spacing:.6px;text-transform:uppercase}
.card{background:var(--white);border-radius:6px;margin:0 7px;padding:9px 8px;box-shadow:0 1px 3px rgba(0,0,0,.05)}
.h{font-size:7px;font-weight:600;margin-bottom:6px}
.lbl{font-size:5.2px;margin-top:5px}
.inp{font-size:4.3px;color:var(--muted);padding:5px 4px;border-bottom:.6px solid var(--line);display:flex;justify-content:space-between;align-items:center}
.btns{display:flex;gap:3px;margin-top:10px}
.ico-btn{width:18px;height:17px;background:var(--olive);border-radius:2px;display:flex;align-items:center;justify-content:center}
.main-btn{flex:1;height:17px;background:var(--olive);border-radius:2px;color:#fff;font-size:5.3px;display:flex;align-items:center;justify-content:center;letter-spacing:.3px}
.link{font-size:5.3px;color:var(--gold);text-decoration:underline;text-align:center;margin-top:9px}
.note{font-size:4.8px;line-height:1.8;text-align:center;padding:0 11px}
.bar{background:var(--header);padding-bottom:6px}
.nav{display:flex;justify-content:space-between;align-items:center;padding:6px 9px 0;font-size:7px}
.nav .t{font-family:"Lexend",sans-serif;font-size:7px}
.nav svg{width:6px;height:6px}
.tabs{position:absolute;left:0;right:0;bottom:0;height:30px;background:var(--white);display:flex;justify-content:space-around;padding:7px 4px 0;border-top:.5px solid var(--line)}
.tabs div{font-size:3.8px;text-align:center;color:#555;line-height:5px}
.tabs svg{width:8px;height:8px;display:block;margin:0 auto 2px}
.p{font-size:4.8px;line-height:1.85;color:#555}
.chk{display:flex;gap:6px;font-size:4.3px;line-height:1.65;color:#444;padding:0 8px}
.chk i{width:6px;height:6px;border:.6px solid #666;flex:none;margin-top:1px}
.tile{background:var(--tile);border-radius:4px;text-align:center;padding:5px 3px}
.tile .d{font-size:3.8px;line-height:5px}
.tile .k{font-size:5.5px;line-height:7px;margin-top:2px}
.tile .v{font-size:5.5px;line-height:7px;margin-top:2px}
.row2{display:flex;gap:4px;margin:0 7px}
.row2 .tile{flex:1}
.mini-card{width:26px;height:17px;border-radius:2px;background:linear-gradient(135deg,#1a5fb4,#0d3c7a 60%,#2d7fd6);flex:none}
.tier{display:flex;gap:6px;align-items:center;background:var(--tile);border-radius:4px;margin:0 7px;padding:5px 5px}
.tier b{font-size:5.5px;line-height:7px;font-weight:600;display:block}
.tier span{font-size:3.6px;line-height:4.6px;color:#555;display:block}
.next{display:flex;gap:6px;align-items:center;padding:0 8px}
.next b{font-size:5.8px;line-height:7px;font-weight:400;display:block}
.next span{font-size:3.6px;line-height:4.6px;display:block}
.total{background:var(--tile);margin:0 7px;border-radius:4px;padding:6px 5px;display:flex;justify-content:space-between;align-items:center}
.total b{font-weight:400;font-size:5.5px;line-height:7px;display:block}
.total span{font-size:3.4px;line-height:4.5px;display:block}
.total em{font-style:normal;font-size:7px}
table{border-collapse:collapse;width:100%;font-size:4.8px}
th,td{border-bottom:.5px solid var(--line);padding:0 8px;height:19.5px;text-align:left}
td+td,th+th{text-align:center;border-left:.5px solid var(--line)}
th{background:#d6cfd0;font-weight:600;height:22px;line-height:1.25}
.tx{background:var(--white);border:.5px solid var(--line);border-radius:3px;margin:0 7px 4px;padding:4px 6px 3px;font-size:4.6px}
.tx .top{display:flex;justify-content:space-between;align-items:center;margin-bottom:2px;line-height:7px}
.tx .badge{background:var(--olive);color:#fff;font-size:3.8px;line-height:5px;padding:1.5px 4px;border-radius:1.5px}
.tx .r{display:flex;justify-content:space-between;line-height:8.5px}
.tx .r.g{color:var(--gold)}
</style>
</head>
<body>

<svg width="0" height="0" style="position:absolute" aria-hidden="true">
  <defs>
    <symbol id="i-home" viewBox="0 0 24 24"><path d="M4 11l8-7 8 7v9h-5v-6H9v6H4z" fill="none" stroke="#333" stroke-width="1.8"/></symbol>
    <symbol id="i-card" viewBox="0 0 24 24"><circle cx="12" cy="8" r="4" fill="none" stroke="#333" stroke-width="1.8"/><path d="M5 21v-3a4 4 0 014-4h6a4 4 0 014 4v3z" fill="none" stroke="#333" stroke-width="1.8"/></symbol>
    <symbol id="i-wallet" viewBox="0 0 24 24"><rect x="3" y="7" width="18" height="13" rx="2" fill="none" stroke="#333" stroke-width="1.8"/><path d="M6 7l9-4 2 4M16 13h3" fill="none" stroke="#333" stroke-width="1.8"/></symbol>
    <symbol id="i-book" viewBox="0 0 24 24"><rect x="3" y="5" width="18" height="16" rx="2" fill="none" stroke="#333" stroke-width="1.8"/><path d="M3 10h18M8 3v4M16 3v4M9 15l2 2 4-4" fill="none" stroke="#333" stroke-width="1.8"/></symbol>
    <symbol id="i-host" viewBox="0 0 24 24"><rect x="4" y="3" width="16" height="18" rx="2" fill="none" stroke="#333" stroke-width="1.8"/><circle cx="12" cy="10" r="3" fill="none" stroke="#333" stroke-width="1.8"/><path d="M7 18a5 5 0 0110 0" fill="none" stroke="#333" stroke-width="1.8"/></symbol>
    <symbol id="i-back" viewBox="0 0 24 24"><path d="M15 4l-8 8 8 8" fill="none" stroke="#222" stroke-width="2.5"/></symbol>
    <symbol id="i-bell" viewBox="0 0 24 24"><path d="M6 17V11a6 6 0 0112 0v6l2 2H4zM10 21h4" fill="#222"/></symbol>
    <symbol id="i-menu" viewBox="0 0 24 24"><path d="M3 6h18M3 12h14M3 18h18" stroke="#222" stroke-width="2.2"/></symbol>
    <symbol id="i-enter" viewBox="0 0 24 24"><circle cx="12" cy="12" r="8" fill="none" stroke="#fff" stroke-width="2"/><path d="M11 8l-4 4 4 4M7 12h10" fill="none" stroke="#fff" stroke-width="2"/></symbol>
    <symbol id="i-eye" viewBox="0 0 24 24"><path d="M2 12s4-6 10-6 10 6 10 6-4 6-10 6S2 12 2 12zM4 20L20 4" fill="none" stroke="#888" stroke-width="2"/></symbol>
    <symbol id="i-stat" viewBox="0 0 40 10"><path d="M1 8h2v1H1zM4 6h2v3H4zM7 4h2v5H7zM10 2h2v7h-2z" fill="#111"/><path d="M16 4a6 6 0 018 0M18 6a3 3 0 014 0" stroke="#111" stroke-width="1.2" fill="none"/><circle cx="20" cy="8" r="1" fill="#111"/><rect x="28" y="2" width="10" height="6" rx="1.5" fill="#111"/></symbol>
  </defs>
</svg>

<div class="title" style="left:7px;top:44px">Login Screen</div>
<div class="title" style="left:200px;top:44px">Sign in Screen</div>
<div class="title" style="left:388px;top:35px">Temp Sign in<br>Screen</div>
<div class="title" style="left:583px;top:44px">Sign Up Screen</div>
<div class="title" style="left:781px;top:45px">Home Screen</div>
<div class="title" style="left:972px;top:46px">Offer Screen</div>
<div class="title" style="left:7px;top:453px">Responsible<br>Screen</div>
<div class="title" style="left:202px;top:453px">Table Limits<br>Screen</div>
<div class="title" style="left:395px;top:452px">Terms &amp; Conditions<br>Screen</div>
<div class="title" style="left:783px;top:436px">Transaction<br>History Screen</div>
<div class="title" style="left:579px;top:560px;width:240px">Terms &amp; Conditions<br>Continue Screen</div>

<!-- Login -->
<section class="phone soft" style="left:37px;top:95px;height:311px">
  <div class="sb"><span>9:41</span><svg viewBox="0 0 40 10"><use href="#i-stat"/></svg></div>
  <div class="brand" style="margin-top:10px"><div class="dot"></div><div class="name">Velvet Circle</div><div class="club">club</div></div>
  <div class="card" style="margin-top:14px;height:210px">
    <div class="h">Member Login</div>
    <div class="lbl">Username</div>
    <div class="inp">Username</div>
    <div class="lbl" style="margin-top:8px">Password</div>
    <div class="inp">Password<svg width="7" height="7"><use href="#i-eye"/></svg></div>
    <div class="btns"><div class="ico-btn"><svg width="9" height="9"><use href="#i-enter"/></svg></div><div class="main-btn">SIGN IN</div></div>
    <div class="link">New Member Login?</div>
    <div style="border-top:.6px solid var(--line);margin-top:8px"></div>
    <div style="text-align:center;font-size:7px;margin-top:9px">OR</div>
    <div style="text-align:center;font-size:5.2px;margin-top:6px">If you are with a temporary ID, sign in here</div>
    <div class="link" style="margin-top:10px">TEMPORARY SIGN IN</div>
  </div>
</section>

<!-- Sign In -->
<section class="phone soft" style="left:230px;top:95px;height:311px">
  <div class="sb"><span>9:41</span><svg viewBox="0 0 40 10"><use href="#i-stat"/></svg></div>
  <div class="brand" style="margin-top:25px"><div class="dot"></div><div class="name">Velvet Circle</div><div class="club">club</div></div>
  <div class="card" style="margin-top:20px;height:157px">
    <div class="h">Sign In</div>
    <div class="lbl">Player ID</div>
    <div class="inp">Player ID</div>
    <div class="lbl" style="margin-top:8px">Pin</div>
    <div class="inp">Pin<svg width="7" height="7"><use href="#i-eye"/></svg></div>
    <div class="btns" style="margin-top:12px"><div class="ico-btn"><svg width="9" height="9"><use href="#i-enter"/></svg></div><div class="main-btn">SIGN IN</div></div>
    <div class="link" style="margin-top:12px">Forgot Password?</div>
  </div>
</section>

<!-- Temp Sign In -->
<section class="phone soft" style="left:423px;top:95px;height:311px">
  <div class="sb"><span>9:41</span><svg viewBox="0 0 40 10"><use href="#i-stat"/></svg></div>
  <div class="brand" style="margin-top:23px"><div class="dot"></div><div class="name">Velvet Circle</div><div class="club">club</div></div>
  <p class="note" style="margin-top:12px">If this is your First time logging in please note the passport No, you used is your Player ID and your Password is your birthday is DD/MM/YYYY format</p>
  <div class="card" style="margin-top:10px;height:135px">
    <div class="h">Sign In</div>
    <div class="lbl">Player ID</div>
    <div class="inp">Player ID ( Password No )</div>
    <div class="lbl" style="margin-top:8px">Pin</div>
    <div class="inp">Pin ( Date of Birth )<span>⌄</span></div>
    <div class="btns" style="margin-top:12px"><div class="ico-btn"><svg width="9" height="9"><use href="#i-enter"/></svg></div><div class="main-btn">SIGN IN</div></div>
  </div>
</section>

<!-- Sign Up -->
<section class="phone" style="left:616px;top:95px;height:442px;background:#eae8e6">
  <div style="background:var(--screen);padding-bottom:8px">
    <div class="sb"><span>9:41</span><svg viewBox="0 0 40 10"><use href="#i-stat"/></svg></div>
    <div style="text-align:center;font-size:7.5px;margin:9px 0 6px">Sign Up</div>
    <div class="card" style="padding:8px;height:150px">
      <div class="lbl" style="margin-top:2px">Last Name / Surname</div>
      <div class="inp" style="border:none;padding:3px 0 18px">( As printed on your velvet circle card or password.)</div>
      <div style="border-top:.6px solid var(--line)"></div>
      <div class="lbl" style="margin-top:9px">First Name</div>
      <div class="inp" style="border:none;padding:3px 0 18px">( As printed on your velvet circle card or password.)</div>
      <div style="border-top:.6px solid var(--line)"></div>
      <div class="lbl" style="margin-top:9px">Date of Birth</div>
      <div class="inp" style="border:none;padding:3px 0">( You need to be atleast 18 years old to join.)</div>
    </div>
    <div class="card" style="margin-top:9px;padding:8px;height:92px">
      <div class="lbl" style="margin-top:2px">Mobile Number</div>
      <div style="display:flex;align-items:center;gap:5px;margin-top:8px;font-size:4.5px">
        <span style="width:10px;height:6px;background:linear-gradient(#d81e25 50%,#fff 50%)"></span>+65 <span style="margin-left:14px">⌄</span>
        <span style="flex:1;border-bottom:.6px solid var(--line);height:8px"></span>
      </div>
      <div class="lbl" style="margin-top:14px">Email Address</div>
      <div style="border-bottom:.6px solid var(--line);height:16px"></div>
    </div>
  </div>
  <div class="chk" style="margin-top:12px"><i></i><div><span style="font-size:5.3px">Marketing Communications ●</span><br>I wish to receive marketing updates via postal mail, email, text messaging and/or telephone as described here. I also consent to KH processing my biometric data and using facial recognition technology for the Purposes.</div></div>
  <div class="chk" style="margin-top:6px"><i></i><div><span style="font-size:5.3px">Terms of Use</span><br>I understand and agree to both the Harbourline programme terms and conditions and the processing of my personal data, and warrant that the declarations here are true.</div></div>
  <div class="main-btn" style="background:var(--disabled);margin:9px 8px 0;height:17px;flex:none">NEXT</div>
</section>

<!-- Home -->
<section class="phone" style="left:809px;top:96px;height:311px">
  <div class="bar" style="padding-bottom:4px">
    <div class="sb"><span>9:41</span><svg viewBox="0 0 40 10"><use href="#i-stat"/></svg></div>
    <div class="nav"><svg><use href="#i-menu"/></svg><span class="t">Velvet Circle</span><svg><use href="#i-bell"/></svg></div>
  </div>
  <div role="img" aria-label="Glamorous EID event banner with festive gold lettering" style="height:51px;background:linear-gradient(160deg,#2a3f8f,#6a4a2c 55%,#c79a3c);position:relative">
    <span style="position:absolute;left:7px;bottom:4px;color:#fff;font-size:5.5px;font-weight:700">Glamorous EID</span>
    <span style="position:absolute;right:8px;bottom:6px;color:#fff;font-size:5px">• • •</span>
  </div>
  <div style="font-size:6px;font-weight:700;padding:9px 8px 5px">Welcome, Guest</div>
  <div style="display:flex;justify-content:space-between;padding:0 6px">
    <div style="text-align:center;font-size:4.5px"><div style="width:17px;height:17px;border-radius:50%;background:#fff;margin:0 auto 3px;box-shadow:0 1px 2px rgba(0,0,0,.15)"></div>My Wallet</div>
    <div style="text-align:center;font-size:4.5px"><div style="width:17px;height:17px;border-radius:50%;background:#fff;margin:0 auto 3px;box-shadow:0 1px 2px rgba(0,0,0,.15)"></div>My Offer</div>
    <div style="text-align:center;font-size:4.5px"><div style="width:17px;height:17px;border-radius:50%;background:#fff;margin:0 auto 3px;box-shadow:0 1px 2px rgba(0,0,0,.15)"></div>Lucky Game</div>
    <div style="text-align:center;font-size:4.5px"><div style="width:17px;height:17px;border-radius:50%;background:#fff;margin:0 auto 3px;box-shadow:0 1px 2px rgba(0,0,0,.15)"></div>My Taxi</div>
    <div style="text-align:center;font-size:4.5px"><div style="width:17px;height:17px;border-radius:50%;background:#fff;margin:0 auto 3px;box-shadow:0 1px 2px rgba(0,0,0,.15);font-size:7px;line-height:14px">•••</div>More</div>
  </div>
  <div style="display:flex;gap:4px;margin:8px 0 0 7px">
    <div style="background:#fff;border-radius:4px;width:134px;height:48px;padding:4px 5px;box-shadow:0 1px 2px rgba(0,0,0,.08);flex:none">
      <div style="font-size:4.3px;font-weight:700">REWARDS 5,972</div>
      <div style="display:flex;gap:4px;margin-top:3px;align-items:center">
        <div class="mini-card" style="width:52px;height:29px"></div>
        <div style="font-size:3.2px;line-height:1.5;color:#666;width:55px"><span style="font-size:4.2px;color:#222">Rewards and loyalty</span><br>If you miss the required points by May 2026, your card level will be moved down.</div>
        <div style="width:10px;height:10px;border-radius:50%;border:.5px solid var(--line);font-size:6px;text-align:center;line-height:9px">→</div>
      </div>
    </div>
    <div style="background:#fff;border-radius:4px;width:20px;height:48px;position:relative"><div style="position:absolute;left:6px;top:12px;width:14px;height:29px;background:#d2232a;border-radius:2px 0 0 2px"></div></div>
  </div>
  <div style="display:flex;justify-content:space-between;font-size:6px;padding:8px 8px 3px"><b style="font-weight:600">● My Offers</b><span style="font-size:4.8px">View All</span></div>
  <div style="display:flex;gap:8px;padding-left:8px;font-size:4.6px;color:#555">
    <div><div role="img" aria-label="Fine dining table with wine glasses" style="width:64px;height:36px;background:linear-gradient(135deg,#cfc3b0,#7a5f45)"></div><div style="margin-top:3px">Dinning</div></div>
    <div><div role="img" aria-label="Spa room with candles" style="width:64px;height:36px;background:linear-gradient(135deg,#8a5b32,#d9a869)"></div><div style="margin-top:3px">Spa</div></div>
    <div><div role="img" aria-label="Package offer photo" style="width:20px;height:36px;background:linear-gradient(135deg,#4a7a35,#c9d6a0)"></div><div style="margin-top:3px">Pack</div></div>
  </div>
  <nav class="tabs"><div><svg><use href="#i-home"/></svg>Home</div><div><svg><use href="#i-card"/></svg>My Card</div><div><svg><use href="#i-wallet"/></svg>My Wallet</div><div><svg><use href="#i-book"/></svg>My Booking</div><div><svg><use href="#i-host"/></svg>My Host</div></nav>
</section>

<!-- Offers -->
<section class="phone" style="left:1001px;top:97px;height:311px">
  <div class="bar">
    <div class="sb"><span>9:41</span><svg viewBox="0 0 40 10"><use href="#i-stat"/></svg></div>
    <div class="nav"><svg><use href="#i-back"/></svg><span class="t">My Offers</span><svg><use href="#i-bell"/></svg></div>
  </div>
  <div style="display:flex;gap:4px;padding:7px 8px;font-size:4.6px;white-space:nowrap">
    <span style="border:.5px solid var(--line);border-radius:8px;padding:3px 7px;background:#fff">☰</span>
    <span style="border:.5px solid var(--line);border-radius:8px;padding:3px 8px;background:#fff">Dining</span>
    <span style="border:.5px solid var(--line);border-radius:8px;padding:3px 10px;background:#fff">Spa</span>
    <span style="border:.5px solid var(--line);border-radius:8px;padding:3px 7px;background:#fff">Package</span>
    <span style="border:.5px solid var(--line);border-radius:8px;padding:3px 7px;background:#fff">Reec</span>
  </div>
  <div style="padding:0 8px">
    <div style="display:flex;gap:7px;padding:3px 0 9px;border-bottom:.5px solid var(--line)"><div role="img" aria-label="Spa massage treatment" style="width:62px;height:35px;background:linear-gradient(135deg,#e9d9c8,#9b7a60)"></div><div style="font-size:3.8px;color:#888;line-height:1.7"><div style="margin-top:2px">Spa</div><div style="font-size:5.6px;color:#111">AYJ Bellinese Spa</div>20% Discount $: Lanemore<br>Hotel spa</div></div>
    <div style="display:flex;gap:7px;padding:9px 0;border-bottom:.5px solid var(--line)"><div role="img" aria-label="Hotel lounge interior" style="width:62px;height:35px;background:linear-gradient(135deg,#b8b2ab,#5d4f45)"></div><div style="font-size:3.8px;color:#888;line-height:1.7"><div style="margin-top:2px">Spa</div><div style="font-size:5.6px;color:#111">12 Star</div>15% Discount $: Kestrane Combo<br>Hotel spa</div></div>
    <div style="display:flex;gap:7px;padding:9px 0;border-bottom:.5px solid var(--line)"><div role="img" aria-label="Candlelit dining table with glasses" style="width:62px;height:35px;background:linear-gradient(135deg,#3a2a1c,#c58a3d)"></div><div style="font-size:3.8px;color:#888;line-height:1.7"><div style="margin-top:2px">Dining</div><div style="font-size:5.6px;color:#111">YUB Bellinese Dining</div>20% Discount $: Lanemore<br>Hotel dining</div></div>
    <div style="display:flex;gap:7px;padding:9px 0"><div role="img" aria-label="Spa facial treatment with flowers" style="width:62px;height:35px;background:linear-gradient(135deg,#8a3a3a,#e6b99a)"></div><div style="font-size:3.8px;color:#888;line-height:1.7"><div style="margin-top:2px">Spa</div><div style="font-size:5.6px;color:#111">Bellinese Spa</div>20% Discount $: Lanemore<br>Hotel spa</div></div>
  </div>
  <nav class="tabs"><div><svg><use href="#i-home"/></svg>Home</div><div><svg><use href="#i-card"/></svg>My Card</div><div><svg><use href="#i-wallet"/></svg>My Wallet</div><div><svg><use href="#i-book"/></svg>My Booking</div><div><svg><use href="#i-host"/></svg>My Host</div></nav>
</section>

<!-- Responsible Gaming -->
<section class="phone" style="left:37px;top:524px;height:373px">
  <div class="bar" style="padding:7px 0 6px"><div class="nav" style="padding-top:0"><svg><use href="#i-back"/></svg><span class="t">Responsible Gaming</span><svg><use href="#i-bell"/></svg></div></div>
  <div role="img" aria-label="Abstract light streaks tunnel" style="height:54px;background:radial-gradient(circle at 50% 60%,#0b0f2a 20%,#2b3fa8 55%,#8a2b8e 80%,#151a40)"></div>
  <div class="p" style="padding:10px 8px 0">Kestrane's fully understands the importance of responsible gaming and promotes a sensible,careful behaviouramongst its clients. Our commitments is to a gaming that maintains a healthy atm... We want to see each of our customers to take pleasure in a responsible gaming experience in a friendly and comfortable enviroment.Responsible gaming means that the harmful potential of gambling is minimized and the the players are in the condition of the making sensible,rational choice-with the help...</div>
  <div class="p" style="padding:7px 8px 0">Kestrane's guidelines for responsible gaming are thought out with the pleasant stay of everyone at the casino in mind.A respon...<br>• Is always in control of his/her action.<br>• Has fun and friendly, doesn't view this as a profession or a contest.<br>• Remembers that gambling is a type of entertainment, not a lifelong commitment.<br>• Gambles us ng money that aren't core to his lifestyle i.e. Household income.<br>• Absolutely never relies on borrowing money to gamble.<br>• Has a clear limits on his/her spendings and knows when to stop.<br>• Takes occasional pauses to refresh his mind, body and mood.<br>• Doesn't intrude in what other clients are playing and how they are doing it.</div>
  <nav class="tabs"><div><svg><use href="#i-home"/></svg>Home</div><div><svg><use href="#i-card"/></svg>My Card</div><div><svg><use href="#i-wallet"/></svg>My Wallet</div><div><svg><use href="#i-book"/></svg>My Booking</div><div><svg><use href="#i-host"/></svg>My Host</div></nav>
</section>

<!-- Table Limits -->
<section class="phone" style="left:230px;top:524px;height:373px">
  <div class="bar" style="padding:8px 0 6px"><div class="nav" style="padding-top:0"><svg><use href="#i-back"/></svg><span class="t">Table Limits</span><svg><use href="#i-bell"/></svg></div></div>
  <div role="img" aria-label="Gaming floor with light streaks" style="height:54px;background:radial-gradient(circle at 50% 60%,#0b0f2a 20%,#2b3fa8 55%,#8a2b8e 80%,#151a40);position:relative"><span style="position:absolute;left:8px;bottom:5px;color:#fff;font-size:6px;font-weight:700">Gaming Floor</span></div>
  <div style="margin:9px 7px 0;border:.5px solid var(--line);border-radius:4px;overflow:hidden;background:#fff">
    <table>
      <tr><th>Name</th><th>Min Bet<br>(LKR)</th><th>Max Bet<br>(LKR)</th></tr>
      <tr><td>Baccarat</td><td>1,000</td><td>10,000,000</td></tr>
      <tr><td>Baccarat</td><td>1,000</td><td>20,000,000</td></tr>
      <tr><td>Baccarat</td><td>1,000</td><td>30,000,000</td></tr>
      <tr><td>Baccarat</td><td>1,000</td><td>10,000,000</td></tr>
      <tr><td>Baccarat</td><td>1,000</td><td>20,000,000</td></tr>
      <tr><td>Baccarat</td><td>1,000</td><td>30,000,000</td></tr>
      <tr><td>Baccarat Table Limit</td><td>2,000</td><td>2,000,000</td></tr>
      <tr><td>Baccarat Table Limit</td><td>2,000</td><td>2,000,000</td></tr>
      <tr><td style="border:none">Baccarat Table Limit</td><td style="border-bottom:none">2,000</td><td style="border-bottom:none">2,000,000</td></tr>
    </table>
  </div>
  <div style="display:flex;justify-content:space-between;font-size:5.3px;padding:10px 9px 7px 16px;border-bottom:.5px solid var(--line)"><span>Vip Area</span><span>Min Bet (LKR)</span><span>Max Bet (LKR)</span></div>
  <div style="display:flex;justify-content:space-between;font-size:4.8px;padding:7px 9px 0 16px"><span>Baccarat Table<br>Limit</span><span style="margin-top:3px">2,000</span><span style="margin-top:3px">2,000,000</span></div>
  <nav class="tabs"><div><svg><use href="#i-home"/></svg>Home</div><div><svg><use href="#i-card"/></svg>My Card</div><div><svg><use href="#i-wallet"/></svg>My Wallet</div><div><svg><use href="#i-book"/></svg>My Booking</div><div><svg><use href="#i-host"/></svg>My Host</div></nav>
</section>

<!-- Terms & Conditions -->
<section class="phone" style="left:423px;top:523px;height:374px">
  <div class="bar" style="padding:7px 0 8px"><div class="nav" style="padding-top:0"><svg><use href="#i-back"/></svg><svg><use href="#i-bell"/></svg></div></div>
  <div style="background:linear-gradient(#fff 62%,#e4e0df 62%);padding:10px 0 8px;text-align:center">
    <div style="font-size:6.6px;letter-spacing:.3px">MR. AREN VOSSEL</div>
    <div style="font-size:4.8px;color:var(--muted);margin-top:3px">BM15125</div>
    <div style="margin:7px auto 0;width:120px;height:73px;border-radius:5px;background:linear-gradient(135deg,#3a3a3a,#111);color:#eee;text-align:left;padding:6px 12px">
      <div style="display:flex;justify-content:space-between;align-items:center"><b style="font-size:7px">BANK</b><span style="font-size:3.6px">CREDIT CARD</span></div>
      <div style="width:9px;height:7px;background:#e0b54a;border-radius:1px;margin-top:7px"></div>
      <div style="font-size:7px;letter-spacing:1.2px;margin-top:5px">1234 5678 9012 3456</div>
      <div style="font-size:3.8px;text-align:center;margin-top:3px">12/34</div>
      <div style="font-size:3.6px;margin-top:4px">CARDHOLDER NAME</div>
    </div>
    <div style="font-size:6.6px;margin-top:6px">My Wallet</div>
  </div>
  <div class="row2" style="margin-top:8px">
    <div class="tile"><div class="d">9 May 2025</div><div class="k">Current Tier Points</div><div class="v">0</div></div>
    <div class="tile"><div class="d">9 May 2025</div><div class="k">Last Tier Points</div><div class="v">2,471,450</div></div>
  </div>
  <div class="tier" style="margin-top:5px"><div class="mini-card"></div><div><b>Infinity</b><span>I am 500,000 Kestrane points by May 9 2026 to maintaining Current card level.</span></div></div>
  <div style="font-size:6.4px;padding:8px 7px 4px">Next Card Level</div>
  <div class="next"><div class="mini-card" style="width:34px;height:21px"></div><div><b>Infinity</b><span>Earn 0 Kestrane points to upgrade next card level</span></div></div>
  <div class="total" style="margin-top:8px"><div><b>Total Points Earned</b><span>Jun 11 2005 4:4PM</span></div><em>0</em></div>
  <div class="row2" style="margin-top:6px">
    <div class="tile"><div class="d">11 Jan 2025</div><div class="k">Slot Points Earned</div><div class="v">0</div></div>
    <div class="tile"><div class="d">11 Jan 2025</div><div class="k">Table Points Earned</div><div class="v">0</div></div>
  </div>
</section>

<!-- Terms & Conditions Continue -->
<section class="phone" style="left:615px;top:630px;height:311px">
  <div class="bar" style="padding:7px 0 8px"><div class="nav" style="padding-top:0"><svg><use href="#i-back"/></svg><svg><use href="#i-bell"/></svg></div></div>
  <div style="text-align:center;padding:8px 0 6px;background:#fff">
    <div style="font-size:6.6px;letter-spacing:.3px">MR. AREN VOSSEL</div>
    <div style="font-size:4.8px;color:var(--muted);margin-top:4px">BM15125</div>
  </div>
  <div class="tier" style="background:#eeeceb"><div class="mini-card"></div><div><b>Infinity</b><span>I am 500,000 Kestrane points by May 9 2026 to maintaining Current card level.</span></div></div>
  <div style="font-size:6.4px;padding:7px 7px 4px">Next Card Level</div>
  <div class="next"><div class="mini-card" style="width:34px;height:21px"></div><div><b>Infinity</b><span>Earn 0 Kestrane points to upgrade next card level</span></div></div>
  <div class="total" style="margin-top:6px"><div><b>Total Points Earned</b><span>Jun 11 2005 4:40PM</span></div><em>0</em></div>
  <div class="row2" style="margin-top:5px">
    <div class="tile"><div class="d">11 Jan 2025 4:04PM</div><div class="k">Slot Points Earned</div><div class="v">0</div></div>
    <div class="tile"><div class="d">11 Jan 2025 4:04PM</div><div class="k">Table Points Earned</div><div class="v">0</div></div>
  </div>
  <div style="font-size:5.8px;line-height:8px;padding:5px 7px 4px">Points Breakdown From Total Points<br>Earned Today</div>
  <div class="row2">
    <div class="tile" style="padding:5px 2px"><div class="k">Kestrane Coins</div><div class="d" style="margin-top:2px">Today Ear Points 60</div></div>
    <div class="tile" style="padding:5px 2px"><div class="k">Kestrane Coins</div><div class="d" style="margin-top:2px">Today Ear Points 40</div></div>
  </div>
  <nav class="tabs"><div><svg><use href="#i-home"/></svg>Home</div><div><svg><use href="#i-card"/></svg>My Card</div><div><svg><use href="#i-wallet"/></svg>My Wallet</div><div><svg><use href="#i-book"/></svg>My Booking</div><div><svg><use href="#i-host"/></svg>My Host</div></nav>
</section>

<!-- Transaction History -->
<section class="phone" style="left:809px;top:507px;height:311px">
  <div class="bar" style="padding:7px 0 7px"><div class="nav" style="padding-top:0"><svg><use href="#i-back"/></svg><span class="t">Transaction History</span><svg><use href="#i-bell"/></svg></div></div>
  <div style="padding-top:5px">
    <div class="tx"><div class="top"><span>24 Jun 2023</span><span class="badge">KESTRANE COINS</span></div><div class="r g"><span>Total Rewards Redeemed</span><span>7,000</span></div><div class="r"><span>Ballance Kestrane Coins</span><span>10, 46g</span></div><div class="r"><span>Balance Sri Lankan Rupees</span><span>14, 646</span></div></div>
    <div class="tx"><div class="top"><span>22 Jun 2023</span><span class="badge">SLR</span></div><div class="r g"><span>Total Rewards Redeemed</span><span>7,000</span></div><div class="r"><span>Ballance Kestrane Coins</span><span>10, 662</span></div><div class="r"><span>Balance Sri Lankan Rupees</span><span>10, 108</span></div></div>
    <div class="tx"><div class="top"><span>22 Jun 2023</span><span class="badge">KESTRANE COINS</span></div><div class="r g"><span>Total Rewards Redeemed</span><span>19,000</span></div><div class="r"><span>Ballance Kestrane Coins</span><span>10, 662</span></div><div class="r"><span>Balance Sri Lankan Rupees</span><span>23, 108</span></div></div>
    <div class="tx"><div class="top"><span>22 Jun 2023</span><span class="badge">SLR</span></div><div class="r g"><span>Total Rewards Redeemed</span><span>9,000</span></div><div class="r"><span>Ballance Kestrane Coins</span><span>10, 285</span></div><div class="r"><span>Balance Sri Lankan Rupees</span><span>10, 190</span></div></div>
    <div class="tx"><div class="top"><span>21 Jun 2023</span><span class="badge">KESTRANE COINS</span></div><div class="r g"><span>Total Rewards Redeemed</span><span>13,000</span></div><div class="r"><span>Ballance Kestrane Coins</span><span>10, 285</span></div><div class="r"><span>Balance Sri Lankan Rupees</span><span>10, 190</span></div></div>
  </div>
  <nav class="tabs"><div><svg><use href="#i-home"/></svg>Home</div><div><svg><use href="#i-card"/></svg>My Card</div><div><svg><use href="#i-wallet"/></svg>My Wallet</div><div><svg><use href="#i-book"/></svg>My Booking</div><div><svg><use href="#i-host"/></svg>My Host</div></nav>
</section>

</body>
</html>
```